Harborline Renewal Business Card Design

Professional and clean design. The design colors should flow with the logo. Two-sided card with the website on the back which is:

www.HarborlineRenewal.example.

"Specializing in Water Damage Restoration"

On the front I need the name, email, phone, and logo.

Name: Darnell Quisby
Email: Darnell@HarborlineRenewal.example
Phone: 555-318-2046 for now

I only have the Preview and Thumbnail right now but should have the source files uploaded within a day or two.

Target Market(s)

Flood victims, home owners with water damage from busted pipes etc...

Industry/Entity Type

Business

Contact Information for Business Card

Name: Darnell Quisby

Font styles to use
Serif
Sans Serif

Requirements
Must have
• Business Card Details Info

```html
<!DOCTYPE html>
<html lang="en">
<head>
<meta charset="utf-8">
<title>Harborline Renewal Business Card</title>
<link rel="stylesheet" href="https://fonts.googleapis.com/css2?family=Cinzel:wght@400&family=PT+Sans:wght@400&display=swap">
<style>
  :root {
    --stage: #1c1c1c;
    --card-white: #ffffff;
    --brand-blue: #2696d6;
    --accent-blue: #2a8fd4;
    --light-blue: #58c0ef;
    --ink: #333333;
    --on-blue: #ffffff;
  }
  * { box-sizing: border-box; margin: 0; padding: 0; }
  html, body { width: 1200px; height: 900px; overflow: hidden; }
  body {
    background: var(--stage);
    position: relative;
    font-family: "PT Sans", "Myriad Pro", Arial, sans-serif;
  }
  .card {
    position: absolute;
    top: 170px;
    width: 347px;
    height: 561px;
  }
  .card-front { left: 259px; background: var(--card-white); }
  .card-back { left: 631px; background: var(--brand-blue); }

  .tab {
    position: absolute;
    left: 102px;
    width: 143px;
    height: 30px;
    background: var(--brand-blue);
  }
  .tab-top { top: 0; }
  .tab-bottom { bottom: 0; height: 28px; }

  .brand-mark {
    position: absolute;
    left: 0; right: 0;
    text-align: center;
  }
  .front-mark { top: 82px; }
  .mark-dot {
    display: block;
    margin: 0 auto;
    width: 112px;
    height: 112px;
    border-radius: 50%;
    background: var(--light-blue);
  }
  .front-mark .mark-name {
    display: block;
    margin-top: 16px;
    font-family: "Cinzel", "Trajan Pro", Georgia, serif;
    font-size: 22px;
    color: var(--accent-blue);
    letter-spacing: 1px;
  }

  .holder-name {
    position: absolute;
    top: 276px;
    left: 0; right: 0;
    text-align: center;
    font-size: 26px;
    color: var(--accent-blue);
    text-transform: uppercase;
    letter-spacing: 0.2px;
  }

  .contact-list {
    position: absolute;
    top: 348px;
    left: 0; right: 0;
    list-style: none;
    text-align: center;
    font-size: 15px;
    line-height: 21px;
    color: var(--ink);
  }
  .contact-list li { display: flex; justify-content: center; align-items: center; gap: 9px; }
  .contact-list svg { width: 11px; height: 11px; fill: var(--light-blue); }

  .tagline {
    position: absolute;
    top: 464px;
    left: 0; right: 0;
    text-align: center;
    font-size: 15px;
    line-height: 18px;
    color: var(--ink);
  }

  .back-mark { top: 204px; }
  .back-mark .mark-dot {
    width: 76px; height: 76px;
    background: var(--on-blue);
  }
  .back-mark .mark-name {
    display: block;
    margin-top: 14px;
    font-family: "Cinzel", "Trajan Pro", Georgia, serif;
    font-size: 36px;
    line-height: 40px;
    color: var(--on-blue);
    letter-spacing: 1px;
  }

  .website {
    position: absolute;
    top: 514px;
    left: 0; right: 0;
    text-align: center;
    font-size: 15px;
    color: var(--on-blue);
  }
</style>
</head>
<body>
  <section class="card card-front">
    <div class="tab tab-top"></div>
    <div class="brand-mark front-mark">
      <span class="mark-dot"></span>
      <span class="mark-name">Harborline Renewal</span>
    </div>
    <h1 class="holder-name">Darnell Quisby</h1>
    <ul class="contact-list">
      <li>
        <svg viewBox="0 0 12 12" aria-hidden="true"><path d="M1 4.5C1 3 3 2 6 2s5 1 5 2.5V6H8.5V4.8h-5V6H1zM3 6.5h6L10 10H2z"/></svg>
        <span>555-318-2046</span>
      </li>
      <li>
        <svg viewBox="0 0 12 12" aria-hidden="true"><path d="M1 3h10v6H1zM1.6 3.4 6 6.6l4.4-3.2" stroke="#fff" stroke-width="0.8"/></svg>
        <span>Darnell@HarborlineRenewal.example</span>
      </li>
    </ul>
    <p class="tagline">Specializing in Water Damage<br>Restoration</p>
    <div class="tab tab-bottom"></div>
  </section>

  <section class="card card-back">
    <div class="brand-mark back-mark">
      <span class="mark-dot"></span>
      <span class="mark-name">Harborline<br>Renewal</span>
    </div>
    <p class="website">www.HarborlineRenewal.example</p>
  </section>
</body>
</html>
```